Varentoria Business Card and Letter Head

We are a leadership assessment consultancy based in Sydney, Australia. We help executive-level decison-makers select leaders for more senior level roles in corporate and government organisations. Our methodology is based on the latest research from the field of neuroscience.
We need a business card design and matching letter head that presents our company, Varentoria, as a:
1. trusted adviser to senior executive-level decison makers
2. niche consultancy who are experts in the field of assessing leadership talent
3. results-focused solution provider who balance scientific methods with pragmatic solutions
The following company details should be used in all designs:
Company Name: Varentoria
Details (for business card):
Derek Hanford
Prime Capacity Officer
Level 29, Marlow Tower
7 Marlow Square
Sydney, NSW 2000 Australia
Phone: 1300 582 714
Mobile: 0412 637 258
Email: derek.hanford@varentoria-example.com.au
Website: varentoria-example.com.au
I have attached the logo for Varentoria (for both a white and black background) - your business card and letter head designs must incoporate this logo and colour scheme.
Thanks for your interest in this project, I'm looking forward to receiving your ideas.
Regards,
Derek
Target Market(s)
Executive-level decison-makers in corporate and government organisations (e.g., CEO, VP, Head of Human Resources)
Industry/Entity Type
Leadership
Look and feel

```html
<!DOCTYPE html>
<html lang="en">
<head>
<meta charset="utf-8">
<title>Varentoria Business Card</title>
<link rel="stylesheet" href="https://fonts.googleapis.com/css2?family=Open+Sans:wght@400;600;700;800&display=swap">
<style>
  :root {
    --bg: #ececec;
    --card: #ffffff;
    --ink: #3c3c3c;
    --ink-soft: #5a5a5a;
    --brand-red: #b8301f;
    --rule: #4a4a4a;
    --on-red: #ffffff;
  }
  * { box-sizing: border-box; margin: 0; padding: 0; }
  html, body {
    width: 1200px; height: 1094px; overflow: hidden;
    background: var(--bg);
    font-family: "Open Sans", Arial, sans-serif;
    color: var(--ink);
  }
  .canvas { position: relative; width: 1200px; height: 1094px; }

  .card {
    position: absolute;
    width: 640px; height: 366px;
    background: var(--card);
    border-radius: 26px;
    overflow: hidden;
    box-shadow: 0 6px 18px rgba(0,0,0,0.18);
  }
  .card--front { left: 100px; top: 110px; }
  .card--back  { left: 460px; top: 610px; }

  /* brand lockup */
  .brand { display: flex; align-items: center; gap: 14px; }
  .brand__square { width: 34px; height: 34px; background: var(--brand-red); flex: none; }
  .brand__name { font-weight: 800; font-size: 50px; line-height: 1; color: var(--ink); letter-spacing: -1px; }
  .brand__tagline {
    font-weight: 400; font-size: 14px; letter-spacing: 1.2px;
    color: var(--ink-soft); text-transform: uppercase; margin-top: 4px;
  }

  /* front */
  .front__brand { position: absolute; left: 90px; top: 46px; }
  .front__brand .brand__tagline { margin-left: 48px; }
  .front__address {
    position: absolute; right: 40px; top: 170px;
    font-size: 15px; color: var(--ink);
  }
  .front__rule { position: absolute; left: 0; right: 0; top: 204px; height: 2px; background: var(--rule); }
  .front__band {
    position: absolute; left: 0; right: 0; top: 212px; bottom: 0;
    background: var(--brand-red); color: var(--on-red);
    display: flex; align-items: center;
  }
  .person { width: 250px; text-align: right; padding-right: 22px; }
  .person__name { font-weight: 700; font-size: 19px; }
  .person__title { font-size: 14px; margin-top: 2px; }
  .band__divider { width: 1px; height: 92px; background: rgba(255,255,255,0.7); }
  .contacts { list-style: none; padding-left: 16px; }
  .contacts li { display: flex; align-items: center; gap: 8px; font-size: 13.5px; line-height: 21px; }
  .contacts svg { width: 13px; height: 13px; flex: none; }

  /* back */
  .back__brand { position: absolute; left: 0; right: 0; top: 92px; display: flex; flex-direction: column; align-items: center; }
  .back__brand .brand__name { font-size: 58px; }
  .back__brand .brand__tagline { font-size: 16px; }
  .back__url {
    position: absolute; left: 0; right: 0; top: 262px; text-align: center;
    font-size: 21px; letter-spacing: 2.5px; color: var(--ink);
  }
</style>
</head>
<body>
<main class="canvas">

  <section class="card card--front" aria-label="Business card front">
    <div class="front__brand">
      <div class="brand">
        <span class="brand__square"></span>
        <span class="brand__name">Varentoria</span>
      </div>
      <p class="brand__tagline">Assessing Executive Capability</p>
    </div>
    <p class="front__address">Level 29, Marlow Tower 7 Marlow Square Sydney, NSW 2000 Australia</p>
    <div class="front__rule"></div>
    <div class="front__band">
      <div class="person">
        <p class="person__name">Derek Hanford</p>
        <p class="person__title">Prime Capacity Officer</p>
      </div>
      <div class="band__divider"></div>
      <ul class="contacts">
        <li><svg viewBox="0 0 16 16" aria-hidden="true"><circle cx="8" cy="8" r="7.5" fill="none" stroke="#fff" stroke-width="1.2"/><path d="M5 4.5l1.6-.3.8 2-1 .8a5 5 0 0 0 2.6 2.6l.8-1 2 .8-.3 1.6c-3.4.3-6.8-3.1-6.5-6.5z" fill="#fff"/></svg>1300 582 714</li>
        <li><svg viewBox="0 0 16 16" aria-hidden="true"><rect x="4.5" y="1" width="7" height="14" rx="1.3" fill="#fff"/><rect x="5.8" y="3" width="4.4" height="7" fill="#b8301f"/></svg>0412 637 258</li>
        <li><svg viewBox="0 0 16 16" aria-hidden="true"><rect x="1" y="3.5" width="14" height="9.5" fill="#fff"/><path d="M1 3.5l7 5.5 7-5.5" fill="none" stroke="#b8301f" stroke-width="1.2"/></svg>derek.hanford@varentoria-example.com.au</li>
        <li><svg viewBox="0 0 16 16" aria-hidden="true"><circle cx="8" cy="8" r="7" fill="#fff"/><path d="M1 8h14M8 1c-3 3.5-3 10.5 0 14M8 1c3 3.5 3 10.5 0 14" fill="none" stroke="#b8301f" stroke-width="1"/></svg>www.varentoria-example.com.au</li>
      </ul>
    </div>
  </section>

  <section class="card card--back" aria-label="Business card back">
    <div class="back__brand">
      <div class="brand">
        <span class="brand__square"></span>
        <span class="brand__name">Varentoria</span>
      </div>
      <p class="brand__tagline">Assessing Executive Capability</p>
    </div>
    <p class="back__url">www.varentoria-example.com.au</p>
  </section>

</main>
</body>
</html>
```